Velundra Jobs portal

Velundra Jobs is a job portal connecting job seekers and companies offering part time jobs in the Mena region, starting in the UAE. We would like to see designs that use the color blue. We have attached images to give an idea what the website should look like. When a company posts a job the job seekers are not allowed to see which company has posted a job. There should also be a coinvex gateway. On the landing page we want a catching picture that we will send.

Target Market(s)

Students and promotional workers

Logo Text

Velundra Jobs

Coding

Coded - Design and coding required

Number of Pages Required

4 page

Font styles to use
Sans Serif

Colors
33a6d7
0692cd
85cae6

```html
<!DOCTYPE html>
<html lang="en">
<head>
<meta charset="utf-8">
<title>Velundra Jobs — Welcome</title>
<link href="https://fonts.googleapis.com/css2?family=Open+Sans:wght@400;600&display=swap" rel="stylesheet">
<style>
  :root{
    --stage:#4a7fd0;
    --page:#ffffff;
    --bar-blue:#2f6bbf;
    --bar-pink:#d94a8c;
    --bar-teal:#4fc4c0;
    --overlay:#1b1b1b;
    --ghost:#2a2a2a;
    --employer-top:#5489e0;
    --employer-bottom:#3f72cf;
    --seeker-top:#66c7c8;
    --seeker-bottom:#55b7b9;
    --text-light:#ffffff;
    --text-muted:#e4e4e4;
    --footer-text:#555555;
    --dots:#cfcfcf;
  }
  *{margin:0;padding:0;box-sizing:border-box}
  html,body{width:1200px;height:797px;overflow:hidden}
  body{background:var(--stage);font-family:"Open Sans",Arial,sans-serif;position:relative}
  .page{position:absolute;left:99px;top:53px;width:1003px;height:690px;background:var(--page);overflow:hidden}
  .top-bars{position:absolute;left:0;top:0;width:100%;height:3px;display:flex}
  .top-bars span{flex:1}
  .top-bars .blue{background:var(--bar-blue)}
  .top-bars .pink{background:var(--bar-pink)}
  .top-bars .teal{background:var(--bar-teal)}
  .mascot-decor{position:absolute;left:10px;top:400px;width:200px;height:270px;border-radius:90px 90px 40px 40px;background:linear-gradient(#f3f3f3,#f7f7f7)}
  .overlay{position:absolute;left:111px;top:87px;width:776px;height:459px;background:var(--overlay)}
  .ghost-mascot{position:absolute;left:190px;top:80px;width:120px;height:240px;border-radius:50px;background:linear-gradient(#222,#241c1c)}
  .ghost-copy{position:absolute;left:432px;top:86px;width:235px;font-size:11.5px;line-height:16.5px;color:var(--ghost);text-align:justify}
  .ghost-button{position:absolute;left:432px;top:231px;width:234px;height:45px;background:#121418;color:#1f2228;font-size:21px;display:flex;align-items:center;justify-content:center}
  .welcome{position:absolute;left:0;top:0;width:100%;height:100%;text-align:center;color:var(--text-light)}
  .welcome h1{position:absolute;left:0;right:0;top:132px;font-size:25px;font-weight:600;letter-spacing:.2px}
  .welcome p{position:absolute;left:56px;width:664px;top:178px;font-size:12.6px;line-height:18px;color:var(--text-muted)}
  .choice{position:absolute;top:315px;width:224px;height:45px;color:#fff;font-size:20px;display:flex;align-items:center;justify-content:center;border-radius:2px;box-shadow:0 2px 0 rgba(0,0,0,.35)}
  .choice.employer{left:157px;background:linear-gradient(var(--employer-top),var(--employer-bottom))}
  .choice.seeker{left:397px;background:linear-gradient(var(--seeker-top),var(--seeker-bottom))}
  .or-badge{position:absolute;left:375px;top:322px;width:31px;height:31px;border-radius:50%;background:#fff;color:#333;font-size:14px;font-weight:600;display:flex;align-items:center;justify-content:center}
  .divider{position:absolute;left:72px;top:597px;width:858px;border-top:1px dotted var(--dots)}
  .page-code{position:absolute;left:962px;top:588px;font-size:12.5px;color:#333}
  .footer{position:absolute;top:644px;font-size:12.2px;color:var(--footer-text)}
  .footer.copy{left:164px}
  .footer.links{right:117px;display:flex;gap:12px}
</style>
</head>
<body>
  <div class="page">
    <div class="top-bars"><span class="blue"></span><span class="pink"></span><span class="teal"></span></div>
    <div class="mascot-decor" role="img" aria-label="Faint mascot illustration in the page background"></div>

    <div class="overlay">
      <div class="ghost-mascot" role="img" aria-label="Dimmed mascot illustration behind the welcome dialog"></div>
      <div class="ghost-copy">We are offering part time work across the region, helping students and promoters find flexible shifts with trusted employers, simple sign up, fast replies and fair pay for every job posted here.</div>
      <div class="ghost-button">Join Velundra</div>

      <div class="welcome">
        <h1>Welcome To Our Site</h1>
        <p>Nullam scelerisque est id risus auctor, ut pharetra tellus fermentum. Curabitur eget pulvinar velit. Maecenas tempor sit amet libero ac egestas. Cras cursus eleifend velit, eu vestibulum purus cursus id. Pellentesque orci dui, pulvinar at neque nec, malesuada commodo ipsum. Cras augue ante,</p>
        <div class="choice employer">EMPLOYER</div>
        <div class="choice seeker">JOB SEEKER</div>
        <div class="or-badge">OR</div>
      </div>
    </div>

    <div class="divider"></div>
    <div class="page-code">M3</div>
    <div class="footer copy">Copyrights reserved to velundra 2015</div>
    <div class="footer links"><span>About Us</span><span>|</span><span>Terms and conditions</span><span>|</span><span>Sitemap</span></div>
  </div>
</body>
</html>
```